Marwick Partners Exit Plan business consultant web site

This website is for a consulting business that helps other businesses with exit plans. Essentially, assists them with the sale of their business. This website should be very professional, almost with a wall street look. I would like a very attractive image on the homepage. Perhaps something that denotes success. Perhaps a picture of palm trees and a beach? I will leave it to you for interpretation.

Across the screen I would like the words "Does your business have an exit plan?"

Below that it should read the following:
Let us help you with a completely impartial, no obligation assessment (button with link to the contact page)

Also, please use logo in a prominent place on the website so it's easily seen.

Target Market(s)

Males 40+

Coding

Coded - Design and coding required

Number of Pages Required

5+ page

Colors

Designer to choose colors to be used in the design.

Requirements
Must have
• The tabs for the homepage on the top should be:
• 1. About us
• 2. Services
• 3. Industries
• 4. Our success
• 5. Contact
Nice to have
• Clean, professional image.
• Please put FB, Twitter, Linked In - logos at bottom.
• Here are two examples of a website to give you an idea:
• https://notes.quelvarocapital.example/library/why-every-business-owner-should-have-an-exit-plan
Should not have
• nothing whimsical or cartoon like

```html
<!DOCTYPE html>
<html lang="en">
<head>
<meta charset="utf-8">
<title>Marwick Partners — Exit Planning Consultants</title>
<link rel="stylesheet" href="https://fonts.googleapis.com/css2?family=Oswald:wght@400;500&family=Poppins:wght@300;400;500&family=Open+Sans:wght@400;700&family=Playfair+Display:wght@700&display=swap">
<style>
:root{
  --blue:#1f98d6;
  --black:#000;
  --ink:#111;
  --text:#333;
  --muted:#666;
  --grey:#efefef;
  --navy-shadow:#0b1b2a;
  --white:#fff;
}
*{margin:0;padding:0;box-sizing:border-box}
html,body{width:1200px;height:3635px;overflow:hidden;background:var(--white)}
body{position:relative;font-family:"Poppins",sans-serif;color:var(--text)}
.abs{position:absolute}
.btn{position:absolute;display:flex;align-items:center;justify-content:center;background:var(--blue);color:var(--white);font-family:"Oswald",sans-serif;font-size:21px;text-decoration:none;letter-spacing:.2px}
.photo{position:absolute}

/* header */
.brand{left:76px;top:14px;width:150px;height:78px;display:flex;flex-direction:column;align-items:center;gap:6px}
.brand-mark{width:46px;height:46px;background:var(--black)}
.brand-name{font-family:"Oswald",sans-serif;font-size:17px;color:var(--ink);letter-spacing:.5px;white-space:nowrap}
.nav{left:548px;top:34px;display:flex;gap:24px;font-size:14.5px;color:#333}
.nav .active{position:relative;padding-left:12px;color:var(--ink)}
.nav .active::before{content:"";position:absolute;left:0;top:7px;width:6px;height:6px;background:var(--blue)}
.nav-cta{left:1001px;top:21px;width:123px;height:47px;font-size:18px}

/* hero */
.hero-band{left:27px;top:474px;width:1146px;height:376px;background:var(--black)}
.hero-photo{left:342px;top:138px;width:781px;height:533px;background:linear-gradient(135deg,#dfe8ef 0%,#b9c9d6 35%,#33445f 70%,#1a2740 100%)}
.hero-title{left:75px;top:240px;font-family:"Oswald",sans-serif;font-weight:500;font-size:52px;line-height:58px;color:var(--ink)}
.hero-title span{color:var(--blue)}
.hero-text{left:79px;top:372px;width:420px;font-size:16px;line-height:28px;color:var(--text)}
.hero-cta{left:78px;top:442px;width:213px;height:51px}
.hero-watermark{left:462px;top:712px;font-family:"Playfair Display",serif;font-weight:700;font-size:150px;line-height:150px;color:var(--navy-shadow);letter-spacing:-2px;white-space:nowrap;width:700px;overflow:hidden;height:138px}

/* welcome */
.welcome-band{left:27px;top:850px;width:1146px;height:417px;background:var(--blue)}
.welcome-photo{left:155px;top:912px;width:366px;height:417px;background:linear-gradient(160deg,#d9dfe4 0%,#9fb2c2 40%,#5a6f85 70%,#e8ecef 100%)}
.welcome-kicker{left:594px;top:916px;font-size:21px;color:var(--white)}
.welcome-title{left:592px;top:945px;font-family:"Oswald",sans-serif;font-size:48px;color:var(--white)}
.welcome-text{left:597px;top:1012px;width:430px;font-size:14.5px;line-height:26px;color:var(--white)}
.welcome-cta{left:600px;top:1155px;width:156px;height:52px;background:transparent;border:2px solid var(--white)}

/* services */
.section-kicker{left:0;width:1200px;text-align:center;font-size:20px;color:var(--blue)}
.section-title{left:0;width:1200px;text-align:center;font-family:"Oswald",sans-serif;font-size:48px;color:var(--ink)}
.services-band{left:27px;top:1725px;width:1146px;height:677px;background:var(--grey)}
.services-photo{left:209px;top:1538px;width:782px;height:416px;background:linear-gradient(120deg,#c9b9a4 0%,#e8e5e0 35%,#f4f4f4 60%,#9aa0a6 100%)}
.services-text{left:306px;top:1988px;width:620px;font-size:14.5px;line-height:27px;color:var(--text)}
.checklist{left:306px;top:2089px;list-style:none;font-size:15.5px;color:var(--text)}
.checklist li{height:37.7px;display:flex;align-items:center;gap:17px}
.services-cta{left:306px;top:2289px;width:173px;height:51px}

/* industries */
.industries-sub{left:0;width:1200px;text-align:center;top:2525px;font-family:"Open Sans",sans-serif;font-size:14.5px;color:var(--muted)}
.industry{position:absolute;top:2588px;width:175px;height:165px;background:var(--black);color:var(--white);display:flex;flex-direction:column;align-items:center;justify-content:center;gap:14px;font-family:"Oswald",sans-serif;font-size:20px}
.industry.is-active{background:var(--blue)}
.industry svg{width:60px;height:56px;fill:none;stroke-width:2.2;stroke-linecap:round;stroke-linejoin:round}
.industry.is-active svg{stroke:var(--white)}
.industry:not(.is-active) svg{stroke:var(--blue)}

/* success */
.success-title{left:202px;top:2838px;font-family:"Oswald",sans-serif;font-size:48px;color:var(--ink)}
.success-lead{left:210px;top:2904px;width:360px;font-family:"Open Sans",sans-serif;font-weight:700;font-size:16px;line-height:28px;color:var(--ink)}
.success-text{left:210px;top:2970px;width:400px;font-family:"Open Sans",sans-serif;font-size:14.5px;line-height:27px;color:var(--muted)}
.success-cta{left:210px;top:3091px;width:171px;height:51px}
.success-photo{left:635px;top:2789px;width:424px;height:421px;background:linear-gradient(180deg,#ffffff 0%,#e3e7ea 25%,#5c6f82 55%,#3b4a5a 100%)}

/* contact strip */
.contact-band{left:27px;top:3210px;width:1146px;height:103px;background:var(--blue);display:flex;align-items:center;justify-content:center;gap:18px;color:var(--white);font-family:"Oswald",sans-serif}
.contact-band .ask{font-size:27px}
.contact-band .phone{font-size:43px}

/* footer */
.footer{left:27px;top:3313px;width:1146px;height:322px;background:var(--black)}
.footer-brand{left:0;width:1200px;top:3365px;display:flex;flex-direction:column;align-items:center;gap:8px}
.footer-brand .brand-mark{width:50px;height:50px;background:transparent;border:2px solid var(--white)}
.footer-brand .brand-name{color:var(--white);font-size:18px}
.socials{left:0;width:1200px;top:3471px;display:flex;justify-content:center;gap:8px}
.socials span{width:40px;height:40px;border-radius:50%;background:var(--blue)}
.footer-links{left:0;width:1200px;top:3537px;text-align:center;font-size:14.5px;color:var(--white);word-spacing:2px}
.copyright{left:0;width:1200px;top:3568px;text-align:center;font-size:14.5px;color:var(--white)}
</style>
</head>
<body>

<header>
  <div class="abs brand"><div class="brand-mark"></div><div class="brand-name">MARWICK PARTNERS</div></div>
  <nav class="abs nav">
    <span class="active">Home</span><span>About Us</span><span>Services</span><span>Industries</span><span>Our Success</span>
  </nav>
  <a class="btn nav-cta" href="#contact">CONTACT US</a>
</header>

<section class="hero">
  <div class="abs hero-band"></div>
  <div class="abs hero-watermark">MARWICK</div>
  <div class="photo hero-photo" role="img" aria-label="Two business colleagues reviewing a tablet together in a bright office"></div>
  <h1 class="abs hero-title">Does Your Business<br>Have An <span>Exit Plan?</span></h1>
  <p class="abs hero-text">Lorem Ipsum is simply dummy text of the printing and typesetting industry Lorem Ipsum has been.</p>
  <a class="btn hero-cta" href="#contact">GET STARTED WITH US</a>
</section>

<section class="welcome">
  <div class="abs welcome-band"></div>
  <div class="photo welcome-photo" role="img" aria-label="Consultant leaning over a meeting table with a client"></div>
  <p class="abs welcome-kicker">Welcome To</p>
  <h2 class="abs welcome-title">MARWICK PARTNERS</h2>
  <p class="abs welcome-text">Lorem Ipsum is simply dummy text of the printing and typesetting industry. Lorem Ipsum has been the industry's standard dummy text ever since the 1500s, when an unknown printer took a galley of type and scrambled it to make a type specimen book. I</p>
  <a class="btn welcome-cta" href="#about">LEARN MORE</a>
</section>

<section class="services">
  <p class="abs section-kicker" style="top:1410px">Services</p>
  <h2 class="abs section-title" style="top:1436px">BUSINESSES WITH EXIT PLANS</h2>
  <div class="abs services-band"></div>
  <div class="photo services-photo" role="img" aria-label="Hands typing on a laptop showing analytics charts on a desk"></div>
  <p class="abs services-text">Lorem Ipsum is simply dummy text of the printing and typesetting industry. Lorem Ipsum has been the industry's standard dummy text ever since the 1500s, when an unknown printer took a galley of type.</p>
  <ul class="abs checklist">
    <li><svg width="18" height="14" viewBox="0 0 18 14"><path d="M2 7l5 5 9-10" fill="none" stroke="#1f98d6" stroke-width="3"/></svg>Help you Control when and How you exit.</li>
    <li><svg width="18" height="14" viewBox="0 0 18 14"><path d="M2 7l5 5 9-10" fill="none" stroke="#1f98d6" stroke-width="3"/></svg>Maximize Value</li>
    <li><svg width="18" height="14" viewBox="0 0 18 14"><path d="M2 7l5 5 9-10" fill="none" stroke="#1f98d6" stroke-width="3"/></svg>Minimize Taxes</li>
    <li><svg width="18" height="14" viewBox="0 0 18 14"><path d="M2 7l5 5 9-10" fill="none" stroke="#1f98d6" stroke-width="3"/></svg>Clarify your Transition Choices</li>
    <li><svg width="18" height="14" viewBox="0 0 18 14"><path d="M2 7l5 5 9-10" fill="none" stroke="#1f98d6" stroke-width="3"/></svg>Make you More Financially Prepared</li>
  </ul>
  <a class="btn services-cta" href="#services">LEARN MORE</a>
</section>

<section class="industries">
  <h2 class="abs section-title" style="top:2452px">OUR INDUSTRIES</h2>
  <p class="abs industries-sub">Lorem Ipsum is simply dummy text of the printing and typesetting industry.</p>
  <div class="industry is-active" style="left:130px">
    <svg viewBox="0 0 60 56"><circle cx="30" cy="16" r="11"/><path d="M30 9v14M26 13h6a2 2 0 010 4h-4a2 2 0 000 4h6"/><path d="M6 40h10l10 6h14l12-8"/><path d="M16 36h14a3 3 0 010 6H22"/></svg>
    FINANCE</div>
  <div class="industry" style="left:321px">
    <svg viewBox="0 0 60 56"><path d="M6 50h50"/><path d="M10 48V38M18 48V32M26 48V34M34 48V26M42 48V20M50 48V14"/><path d="M8 30l14-10 10 6 20-16"/><path d="M46 10h6v6"/></svg>
    INVESTMENT</div>
  <div class="industry" style="left:512px">
    <svg viewBox="0 0 60 56"><rect x="14" y="6" width="32" height="44" rx="2"/><path d="M20 16h20M20 24h20M20 32h14M20 40h10"/><path d="M36 42l4 4 8-10"/></svg>
    ATTORNEY</div>
  <div class="industry" style="left:704px">
    <svg viewBox="0 0 60 56"><path d="M4 28L30 8l26 20"/><path d="M12 22v26h36V22"/><path d="M25 48V34h10v14"/><path d="M40 12v6"/></svg>
    REAL-ESTATE</div>
  <div class="industry" style="left:895px">
    <svg viewBox="0 0 60 56"><path d="M30 50C10 36 4 26 4 18A12 12 0 0130 12a12 12 0 0126 6c0 8-6 18-26 32z"/><path d="M8 28h12l4-8 6 16 4-10h18"/></svg>
    HEALTH CARE</div>
</section>

<section class="success">
  <h2 class="abs success-title">OUR SUCCESS</h2>
  <p class="abs success-lead">Lorem Ipsum is simply dummy text of the printing and typesetting industry.</p>
  <p class="abs success-text">Lorem Ipsum is simply dummy text of the printing and typesetting industry. Lorem Ipsum has been the industry's standard dummy text ever since the 1500s, when an unknown printer took a.</p>
  <a class="btn success-cta" href="#success">LEARN MORE</a>
  <div class="photo success-photo" role="img" aria-label="Smiling businessman holding an open laptop"></div>
</section>

<section class="abs contact-band" id="contact">
  <span class="ask">If You Need An Have Any Question For Contact Us Today !</span>
  <svg width="52" height="52" viewBox="0 0 52 52"><circle cx="26" cy="26" r="23" fill="none" stroke="#fff" stroke-width="2.5"/><path d="M18 15l5 0 2 7-3 2c2 4 4 6 8 8l2-3 7 2 0 5c-1 2-3 2-5 2-10-1-17-8-18-18 0-2 0-4 2-5z" fill="#fff"/></svg>
  <span class="phone">123 456 7890</span>
</section>

<footer>
  <div class="abs footer"></div>
  <div class="abs footer-brand"><div class="brand-mark"></div><div class="brand-name">MARWICK PARTNERS</div></div>
  <div class="abs socials" aria-label="Social links"><span></span><span></span><span></span></div>
  <p class="abs footer-links">About Us &nbsp;|&nbsp; Services &nbsp;|&nbsp; Industries &nbsp;|&nbsp; Our Success &nbsp;|&nbsp; Contact</p>
  <p class="abs copyright">©MARWICK PARTNERS - 2020 All rights reserved.</p>
</footer>

</body>
</html>
```